new business card

please see the attached business card and logo files, and make the following changes
1-- the little rock clinic address has changed to " suite 287"

2-- lets not " box" the logo

3-- create a " three dimensional " feel of the logo

Target Market(s)

patients and other physicians

Industry/Entity Type

Health Care

Contact Information for Business Card

see the attached files and instructions listed above

Requirements
Must have
• " Vennard Oakhurst Institute" is the parent organization and therefore has a "center piece" role.
Nice to have
• would like to see a three dimensional feel in the logo
Should not have
• feminine colors -- pink etc.

```html
<!DOCTYPE html>
<html lang="en">
<head>
<meta charset="utf-8">
<title>Vennard Oakhurst Institute – Business Card</title>
<link rel="stylesheet" href="https://fonts.googleapis.com/css2?family=Jost:wght@400;500;600&family=Libre+Baskerville:wght@700&display=swap">
<style>
  :root {
    --backdrop: #9b9b9b;
    --card-paper: #ececee;
    --navy: #212e3a;
    --ink: #2b3640;
    --ink-soft: #4a535c;
    --accent: #9a2a78;
    --mark-light: #e6e6e8;
  }
  * { margin: 0; padding: 0; box-sizing: border-box; }
  html, body {
    width: 1105px;
    height: 1200px;
    overflow: hidden;
    background: var(--backdrop);
  }
  .canvas { position: relative; width: 1105px; height: 1200px; }

  .card {
    position: absolute;
    left: 182px;
    width: 747px;
    height: 425px;
    overflow: hidden;
  }
  .card--front { top: 119px; background: var(--card-paper); }
  .card--back { top: 635px; height: 428px; background: var(--navy); }

  .name-flag {
    position: absolute;
    left: 0; top: 52px;
    width: 11px; height: 30px;
    background: var(--navy);
  }
  .doctor-name {
    position: absolute;
    left: 35px; top: 50px;
    font-family: "Libre Baskerville", serif;
    font-weight: 700;
    font-size: 25px;
    color: var(--ink);
    letter-spacing: 0.2px;
  }

  .office { position: absolute; left: 35px; font-family: "Jost", sans-serif; }
  .office--little-rock { top: 94px; }
  .office--pine-bluff { top: 256px; }
  .office-title {
    font-weight: 600;
    font-size: 19px;
    color: var(--ink);
    line-height: 26px;
  }
  .office-address {
    font-weight: 400;
    font-size: 19px;
    color: var(--ink-soft);
    line-height: 26px;
  }
  .office-lines { list-style: none; margin-top: 8px; }
  .office-line {
    display: flex;
    align-items: center;
    gap: 8px;
    font-size: 19px;
    color: var(--ink-soft);
    line-height: 28px;
  }
  .office-line svg { width: 16px; height: 16px; fill: var(--navy); flex: none; }

  .brand {
    position: absolute;
    right: 48px;
    top: 262px;
    display: flex;
    align-items: center;
    gap: 12px;
  }
  .brand-square { width: 34px; height: 34px; background: var(--navy); }
  .brand-name {
    font-family: "Jost", sans-serif;
    font-weight: 500;
    font-size: 23px;
    color: var(--navy);
  }

  .rule-accent {
    position: absolute;
    left: 0; right: 0; top: 399px;
    height: 2px;
    background: var(--accent);
  }
  .band-base {
    position: absolute;
    left: 0; right: 0; bottom: 0;
    height: 19px;
    background: var(--navy);
  }

  .back-mark {
    position: absolute;
    left: 585px;
    top: 199px;
    width: 117px;
    height: 117px;
    background: var(--mark-light);
  }
</style>
</head>
<body>
<main class="canvas">
  <section class="card card--front" aria-label="Business card front">
    <span class="name-flag"></span>
    <h1 class="doctor-name">Daniel Rourke M.D.</h1>

    <div class="office office--little-rock">
      <p class="office-title">Little Rock office</p>
      <p class="office-address">612B W. Lindell Ave.<br>Suite 287, 72219</p>
      <ul class="office-lines">
        <li class="office-line">
          <svg viewBox="0 0 16 16" aria-hidden="true"><path d="M3.6 1.2l2.3 2.6-1.2 1.8c.9 2 2.6 3.7 4.6 4.6l1.8-1.2 2.6 2.3-1.4 2.5C7 13.4 2.6 9 1.2 3z"/></svg>
          501.555.0142
        </li>
        <li class="office-line">
          <svg viewBox="0 0 16 16" aria-hidden="true"><path d="M4 1h7l1 1v4H4z M1 7h14v6H1z M4 11h8v4H4z"/></svg>
          501.555.0187
        </li>
      </ul>
    </div>

    <div class="office office--pine-bluff">
      <p class="office-title">Pine Bluff office</p>
      <p class="office-address">2875 N. Cedarline St. 71608</p>
      <ul class="office-lines">
        <li class="office-line">
          <svg viewBox="0 0 16 16" aria-hidden="true"><path d="M3.6 1.2l2.3 2.6-1.2 1.8c.9 2 2.6 3.7 4.6 4.6l1.8-1.2 2.6 2.3-1.4 2.5C7 13.4 2.6 9 1.2 3z"/></svg>
          870.555.0163
        </li>
        <li class="office-line">
          <svg viewBox="0 0 16 16" aria-hidden="true"><path d="M4 1h7l1 1v4H4z M1 7h14v6H1z M4 11h8v4H4z"/></svg>
          870.555.0119
        </li>
      </ul>
    </div>

    <div class="brand">
      <span class="brand-square"></span>
      <span class="brand-name">Vennard Oakhurst Institute</span>
    </div>

    <span class="rule-accent"></span>
    <span class="band-base"></span>
  </section>

  <section class="card card--back" aria-label="Business card back">
    <span class="back-mark"></span>
  </section>
</main>
</body>
</html>
```